Homepage mockup for RoutineVerdict.com

I would like a homepage mockup of routineverdict.com.

Basically what the site does, is it allows a person to upload a video of a gymnastics routine and our certified judges will judge the routine providing a score, as well as provide a critique and feedback as to why they gave you that score. Many times people don't know why they got the score they did at a gymnastics competition, so this site aims to provide reasoning behind it.

I have started to design the homepage myself (see attached), and like it, but I'd like a professional to finish the layout, or even come up with something really wow and original. I like clean, typically simple design.

THIS IS AN OLD VERSION OF THE SITE (http://esite.kelpradia.com/) This should only be used so you can get an idea of what the site is about. I DO NOT want the new site to look like this, but the basic concept and content remains the same.

DESIGNER FILES CAN BE DOWNLOADED HERE (http://kelpradia.com/files.aspx)

Target Market(s)

Gymnastic type people, parents of gymnasts, coaches, etc.

Industry/Entity Type

It Professional

Requirements
Must have
• -Routine verdict logo (provided)
-Not required, but I have attached the main photo I used in my mockup (AI File)
*A step by step graphic(s) depicting the process for a user. A How it works sort of explanation. Should be eye catching, not just text.

-Step 1: Videotape your gymnastic routine.
-Step 2: Create an account and share us your video.
-Step 3: Our certified judges will score and critique your routine, fully explaining the reasons behind their score.

```html
<!DOCTYPE html>
<html lang="en">
<head>
<meta charset="utf-8">
<title>RoutineVerdict.com – Home</title>
<link href="https://fonts.googleapis.com/css2?family=Ubuntu:wght@400;500;700&family=Hind:wght@400;500;600&family=Oswald:wght@500&display=swap" rel="stylesheet">
<style>
:root{
  --blue:#1f4fa0;
  --blue-dark:#183f86;
  --blue-text:#1b3f9a;
  --red:#d9391c;
  --red-btn:#d2401e;
  --grey:#555;
  --grey-light:#777;
  --line:#e2ddd6;
  --box-border:#eee6dc;
}
*{box-sizing:border-box;margin:0;padding:0}
html,body{width:967px;height:1200px;overflow:hidden;background:#fff}
body{position:relative;font-family:"Hind",sans-serif;color:var(--grey)}
.abs{position:absolute}

.site-header{left:0;top:0;width:967px;height:113px;background:linear-gradient(#2a5cb0,#1d4c9d)}
.brand{left:46px;top:34px;color:#fff;font:700 30px/1 "Ubuntu",sans-serif;display:flex;align-items:center;gap:10px}
.brand-dot{width:14px;height:14px;border-radius:50%;background:#fff}
.social{right:80px;top:18px;display:flex;gap:4px}
.social span{width:22px;height:22px;border-radius:50%;background:#fff;display:block}
.main-nav{right:0;top:60px;height:53px;display:flex}
.main-nav a{color:#fff;text-decoration:none;font:400 13.5px/53px "Ubuntu",sans-serif;padding:0 16px;border-left:1px solid rgba(255,255,255,.15)}
.main-nav a:first-child{border-left:0}

.hero{left:0;top:113px;width:967px;height:422px;background:linear-gradient(#eeeeed,#fafafa 60%,#fff)}
.hero-photo{left:552px;top:130px;width:415px;height:380px;background:radial-gradient(ellipse at 55% 50%,#c9b6a4,#e8ddd3 55%,rgba(250,250,250,0) 75%)}
.hero-cards{left:380px;top:268px;width:228px;height:185px;background:radial-gradient(ellipse,#ece6d6,#f3efe6 60%,rgba(250,250,250,0) 75%)}
.beam{left:0;top:484px;width:967px;height:51px;background:linear-gradient(#e9ddd0,#d7c3ad 50%,#e5d8ca)}
.hero-title{left:47px;top:170px;font:400 28px/1.2 "Hind",sans-serif;color:var(--blue-text)}
.hero-title b{font-weight:600}
.hero-sub{left:49px;top:210px;font:400 17.5px/1.3 "Hind",sans-serif;color:var(--red)}
.hero-sub2{left:49px;top:236px;font:600 17.5px/1.3 "Hind",sans-serif;color:var(--red)}
.hero-lead{left:49px;top:270px;font:400 12.5px/1.3 "Hind",sans-serif;color:var(--blue-text)}
.hero-copy{left:49px;top:294px;width:330px;font:400 11px/17px "Hind",sans-serif;color:var(--blue-text);text-align:justify}
.cta-wrap{left:42px;top:359px;width:222px;height:58px;border-radius:14px;background:#e3e3e3}
.cta{left:50px;top:367px;width:208px;height:42px;border-radius:10px;background:linear-gradient(#3466c2,#1c47a0);color:#fff;display:flex;align-items:center;padding-left:8px;gap:10px}
.cta small{font:500 10px/1 "Ubuntu",sans-serif;text-align:center}
.cta strong{font:500 19px/1 "Oswald",sans-serif}

.step{top:555px;width:285px;height:190px;border:1px solid var(--box-border);border-radius:8px;background:linear-gradient(#fff,#fbf8f4);padding:24px 22px 0;box-shadow:0 14px 12px -12px rgba(210,150,120,.35)}
.step h2{font:400 20px/1 "Hind",sans-serif;color:#333;margin-bottom:20px}
.step h2 b{font-weight:600}
.step h3{font:600 11px/1.2 "Hind",sans-serif;color:#555;margin-bottom:10px;white-space:nowrap;overflow:hidden}
.step p{font:400 11px/17px "Hind",sans-serif;color:var(--grey-light);height:56px}
.step .btn{display:inline-block;margin-top:8px;background:linear-gradient(#e85630,#c8361a);color:#fff;font:500 12px/25px "Oswald",sans-serif;padding:0 18px;border-radius:13px}
.step svg{position:absolute;right:48px;top:16px}

.divider{left:41px;top:782px;width:884px;height:1px;background:var(--line)}
.vsep{top:811px;width:1px;height:320px;background:var(--line)}
.col{top:806px;width:270px}
.col h2{font:400 20px/1 "Hind",sans-serif;color:var(--blue-text);margin:0 0 18px 6px}
.col h3{font:500 12.5px/1.2 "Hind",sans-serif;color:#333;margin-bottom:12px}
.col p{font:400 10.5px/17px "Hind",sans-serif;color:var(--grey);margin-bottom:9px}
.post h3{color:var(--red)}
.post{margin-bottom:18px}
.post p{font-style:italic;color:var(--grey-light)}
.video{display:flex;gap:12px;margin-bottom:18px}
.thumb{width:93px;height:73px;flex:none;background:linear-gradient(#5b6f92,#1f2a3f);display:flex;align-items:center;justify-content:center}
.thumb i{width:26px;height:26px;border:2px solid #fff;border-radius:50%;display:block;position:relative}
.thumb i:after{content:"";position:absolute;left:9px;top:6px;border-left:9px solid #fff;border-top:5px solid transparent;border-bottom:5px solid transparent}
.video h4{font:400 11.5px/1.2 "Hind",sans-serif;color:var(--blue-text);margin-bottom:4px}
.video p{font:italic 400 10px/17px "Hind",sans-serif;color:var(--blue-text);margin:0}
.video .pts{font-style:normal;margin-top:2px}

.site-footer{left:0;top:1136px;width:967px;height:64px;background:var(--blue-dark);color:#fff}
.site-footer .copy{left:44px;top:23px;font:400 10.5px/1 "Hind",sans-serif}
.site-footer nav{right:30px;top:23px;display:flex;gap:26px}
.site-footer a{color:#fff;text-decoration:none;font:400 10.5px/1 "Hind",sans-serif}
</style>
</head>
<body>
<header class="abs site-header">
  <div class="abs brand"><span class="brand-dot"></span>Routine Verdict</div>
  <div class="abs social"><span></span><span></span><span></span><span></span></div>
  <nav class="abs main-nav">
    <a href="#">Home</a><a href="#">About</a><a href="#">How it Works</a><a href="#">FAQ</a><a href="#">Sample Critique</a><a href="#">Member Area</a>
  </nav>
</header>

<section class="abs hero"></section>
<div class="abs beam" role="img" aria-label="Balance beam in the hero photo"></div>
<div class="abs hero-photo" role="img" aria-label="Gymnast performing a handstand split on a balance beam"></div>
<div class="abs hero-cards" role="img" aria-label="Score cards 8, 7.5 and 6.5 pinned with darts"></div>
<h1 class="abs hero-title">Being <b>Judge</b> Has Never Been <b>Easier</b>..</h1>
<p class="abs hero-sub">Our Judges only give you a Numbers</p>
<p class="abs hero-sub2">We explain there reasons..</p>
<p class="abs hero-lead">Lorem ipsum dolor sit amet, consectetuer adipiscing elit.</p>
<p class="abs hero-copy">Nam cursus. Morbi ut mi. Nullam enim leo, egestas id, condimentum at laoreet mattis, massa. Sed eleifend nonummy diam. Praesent mauris ante, elementum et, bibendum at, posuere.</p>
<div class="abs cta-wrap"></div>
<a class="abs cta" href="#"><small>Upload your video<br>&amp; get critiqued!</small><strong>Get started</strong></a>

<article class="abs step" style="left:41px">
  <h2>Record Your <b>Video</b></h2>
  <h3>Videotape your gymnastic</h3>
  <p>Aliquam nec erat at purus cursus interdum. Vestibulum ligula augue, bibendum accumsan, vestibulum ut, commodo a, mi.</p>
  <span class="btn">CLICK HERE</span>
  <svg width="44" height="36" viewBox="0 0 44 36"><rect x="10" y="10" width="34" height="22" rx="3" fill="#1f4fa0"/><path d="M0 14 10 18v8L0 30z" fill="#1f4fa0"/><rect x="24" y="2" width="14" height="9" rx="2" fill="#1f4fa0"/><rect x="22" y="16" width="14" height="8" rx="1" fill="#fff"/></svg>
</article>
<article class="abs step" style="left:342px">
  <h2 style="margin-top:-4px">Sign up and <b>Upload</b></h2>
  <h3>Create an account and share us your video.</h3>
  <p>Create an account and share us your video Vestibulum ligula augue, bibendum accumsan, vestibulum ut, commodo a, mi.</p>
  <span class="btn">CLICK HERE</span>
  <svg width="52" height="56" viewBox="0 0 52 56" style="right:32px;top:12px"><path d="M26 2 50 14v28L26 54 2 42V14z" fill="#1f4fa0"/><path d="M26 14v26M17 23l9-9 9 9" stroke="#fff" stroke-width="4" fill="none"/></svg>
</article>
<article class="abs step" style="left:640px">
  <h2 style="margin-top:-4px">Get the <b>Why</b></h2>
  <h3>Our certified judges will score</h3>
  <p>Our certified judges will score and critique your routine, fully explaining the reasons behind their score. accumsan, vestibulum ut.</p>
  <span class="btn">CLICK HERE</span>
  <svg width="58" height="58" viewBox="0 0 58 58" style="right:40px;top:12px"><circle cx="29" cy="29" r="26" fill="none" stroke="#1f4fa0" stroke-width="5"/><path d="M20 22a9 9 0 1 1 13 8c-3 2-4 3-4 7" fill="none" stroke="#1f4fa0" stroke-width="5"/><circle cx="29" cy="45" r="3.2" fill="#1f4fa0"/></svg>
</article>

<div class="abs divider"></div>
<div class="abs vsep" style="left:323px"></div>
<div class="abs vsep" style="left:630px"></div>

<section class="abs col" style="left:41px">
  <h2>About Our Website</h2>
  <h3>Vestibulum ligula augue, bibendum accumsan</h3>
  <p>Phasellus felis dolor, scelerisque a, tempus eget, lobortis id, libero. Donec scelerisque leo ac risus. Praesent sit amet est. In dictum, dolor eu dictum porttitor, enim felis viverra mi, eget luctus massa purus quis odio.</p>
  <p>Etiam nulla massa, pharetra facilisis, volutpat in, imperdiet sit amet, sem. Aliquam nec erat at purus cursus interdum. Vestibulum ligula augue, bibendum accumsan, vestibulum ut, commodo a, mi.</p>
  <p>Morbi ornare gravida elit. Integer congue, augue et malesuada iaculis, ipsum dui aliquet felis, at cursus magna nisl nec elit. Donec iaculis diam a nisi.</p>
</section>

<section class="abs col" style="left:348px">
  <h2>Recent Posts</h2>
  <div class="post"><h3>Vestibulum ligula augue, bibendum accumsan</h3><p>Phasellus felis dolor, scelerisque a, tempus eget, lobortis id, libero. Donec scelerisque leo ac risus. Praesent sit amet est. In dictum, dolor eu dictum porttitor</p></div>
  <div class="post"><h3>Duis sed tellus et tortor vestibulum gravida</h3><p>Phasellus felis dolor, scelerisque a, tempus eget, lobortis id, libero. Donec scelerisque leo ac risus.</p></div>
  <div class="post"><h3>Vestibulum ligula augue, bibendum accumsan</h3><p>Phasellus felis dolor, scelerisque a, tempus eget, lobortis id, libero. Donec scelerisque leo ac risus. Praesent sit amet est. In dictum, dolor eu dictum porttitor</p></div>
</section>

<section class="abs col" style="left:654px">
  <h2>Best Rated Vidoes</h2>
  <div class="video"><div class="thumb" role="img" aria-label="Video still of a gymnast on the floor"><i></i></div><div><h4>Video Tittle here</h4><p>Phasellus felis dolor, scelerisque a, tempus eget, lobortis id</p><p class="pts">Points:&nbsp; 8</p></div></div>
  <div class="video"><div class="thumb" role="img" aria-label="Video still of a gymnast leaping"><i></i></div><div><h4>Video Tittle here</h4><p>Phasellus felis dolor, scelerisque a, tempus eget, lobortis id</p><p class="pts">Points:&nbsp; 8</p></div></div>
  <div class="video"><div class="thumb" role="img" aria-label="Video still of a gymnast on the rings"><i></i></div><div><h4>Video Tittle here</h4><p>Phasellus felis dolor, scelerisque a, tempus eget, lobortis id</p><p class="pts">Points:&nbsp; 8</p></div></div>
</section>

<footer class="abs site-footer">
  <p class="abs copy">Copyright © 2012 Company Name.&nbsp; All right reserved</p>
  <nav class="abs"><a href="#">Home</a><a href="#">About</a><a href="#">How it Works</a><a href="#">FAQ</a><a href="#">Sample Critique</a><a href="#">Member Area</a></nav>
</footer>
</body>
</html>
```